Verodex business card

Business card for sustainable investment company called "Verodex". Verodex is an exchange platform selling carbon credits between buyers and sellers. Carbon Credits are an environmental commodity for reducing global carbon emissions.

the card should obviously have our logo and the theme should be sustainability/environment mixed with a trading platform.

Contact Information for Business Card

Logo, Name, Title, Phone, Email

Colors
0054AA
0677BA
7BADD7
CADEEF
E8F1F8
0094D4
00A9DD
6FCCEA
C7EBF8
E9F6FB
00AB8E
00BBA5
67D7C9
C6EFE9
E9F9F6
59FF00
82FF00
B8FF75
E3FFCB
F4FFEA

```html
<!DOCTYPE html>
<html lang="en">
<head>
<meta charset="utf-8">
<title>Verodex Business Card</title>
<link href="https://fonts.googleapis.com/css2?family=Urbanist:wght@400;500;600;700&display=swap" rel="stylesheet">
<style>
  :root {
    --page-bg: #e7e7e5;
    --card-dark: #1a2943;
    --card-light: #2f4662;
    --accent: #3f9bc7;
    --accent-deep: #4a7fc4;
    --text-light: #f2f4f7;
    --text-soft: #dfe5ee;
  }
  * { margin: 0; padding: 0; box-sizing: border-box; }
  html, body {
    width: 1200px; height: 1200px; overflow: hidden;
    background: var(--page-bg);
    font-family: "Urbanist", Arial, sans-serif;
  }
  .card {
    position: absolute;
    left: 234px;
    width: 731px;
    height: 418px;
    background: linear-gradient(200deg, var(--card-light) 0%, var(--card-dark) 70%);
  }
  .card-front { top: 160px; }
  .card-back { top: 632px; }

  .front-brand {
    position: absolute;
    left: 0; right: 0; top: 209px;
    transform: translateY(-50%);
    display: flex; align-items: center; justify-content: center; gap: 22px;
  }
  .brand-square {
    width: 46px; height: 46px;
    background: var(--accent);
    border-radius: 4px;
  }
  .front-name {
    color: var(--text-light);
    font-weight: 700;
    font-size: 62px;
    letter-spacing: 2px;
    line-height: 1;
  }

  .back-brand {
    position: absolute;
    right: 47px; top: 82px;
    display: flex; align-items: center; gap: 14px;
  }
  .back-brand .brand-square { width: 40px; height: 40px; }
  .back-name {
    color: var(--accent);
    font-weight: 700;
    font-size: 52px;
    line-height: 1;
  }

  .person {
    position: absolute; left: 48px; top: 212px;
  }
  .person-name {
    color: var(--accent);
    font-weight: 700;
    font-size: 34px;
    line-height: 40px;
  }
  .person-title {
    color: var(--text-soft);
    font-size: 20px;
    line-height: 26px;
    margin-top: 2px;
  }
  .contact-list {
    list-style: none;
    margin-top: 12px;
  }
  .contact-list li {
    display: flex; align-items: center; gap: 8px;
    color: var(--text-soft);
    font-size: 20px;
    line-height: 27.5px;
  }
  .contact-icon { width: 15px; height: 15px; flex: none; }

  .office {
    position: absolute; right: 48px; top: 317px;
    text-align: right;
    color: var(--text-soft);
    font-size: 20px;
    line-height: 27.5px;
  }
  .office-title { font-weight: 600; color: var(--text-light); }
</style>
</head>
<body>
  <section class="card card-front">
    <div class="front-brand">
      <span class="brand-square"></span>
      <span class="front-name">VERODEX</span>
    </div>
  </section>

  <section class="card card-back">
    <div class="back-brand">
      <span class="brand-square"></span>
      <span class="back-name">Verodex</span>
    </div>

    <div class="person">
      <h1 class="person-name">Mark Halden</h1>
      <p class="person-title">Sales Representative</p>
      <ul class="contact-list">
        <li>
          <svg class="contact-icon" viewBox="0 0 24 24" fill="var(--accent)"><path d="M6.6 10.8a15.1 15.1 0 0 0 6.6 6.6l2.2-2.2a1 1 0 0 1 1-.25 11.4 11.4 0 0 0 3.6.57 1 1 0 0 1 1 1V20a1 1 0 0 1-1 1A17 17 0 0 1 3 4a1 1 0 0 1 1-1h3.5a1 1 0 0 1 1 1c0 1.25.2 2.45.57 3.57a1 1 0 0 1-.25 1z"/></svg>
          +36 30 555 0142
        </li>
        <li>
          <svg class="contact-icon" viewBox="0 0 24 24" fill="var(--accent-deep)"><path d="M2 5h20v14H2z"/><path d="M2 5l10 8 10-8" fill="none" stroke="var(--card-dark)" stroke-width="2"/></svg>
          szerviz@verodex.com
        </li>
        <li>
          <svg class="contact-icon" viewBox="0 0 24 24" fill="none" stroke="var(--accent)" stroke-width="2"><circle cx="12" cy="12" r="10"/><path d="M2 12h20M12 2c3 3 3 17 0 20M12 2c-3 3-3 17 0 20"/></svg>
          www.verodex.com
        </li>
      </ul>
    </div>

    <address class="office" style="font-style:normal">
      <div class="office-title">Verodex Head Office</div>
      <div>Budapest XIII. Fenyves utca 12.</div>
    </address>
  </section>
</body>
</html>
```